Business card for law firm

Need business card for new law firm. Think confident, authoritative, conservative, but not stuffy or old-fashioned.

Contact Information for Business Card

Content for card - logo (uploaded), plus the following:

Paul Whitcombe (larger font)
Managing Partner (larger font, but not as large as name)
Level 9, 7 Ferris Lane
Sydney NSW 2000
Main Tel 02 9364 2710
Direct Tel 02 8472 3159
Email paul@qvlegal.com.au
www.qvlegal.com.au

Letterhead design should include logo plus:
Level 9, 7 Ferris Lane
Sydney NSW 2000
Tel 02 8472 3159
www.qvlegal.com.au

```html
<!DOCTYPE html>
<html lang="en">
<head>
<meta charset="utf-8">
<title>Quayvale Lawyers – Business Card</title>
<link rel="stylesheet" href="https://fonts.googleapis.com/css2?family=Tinos:wght@400&display=swap">
<style>
  :root {
    --navy: #0f2a78;
    --navy-deep: #0a2266;
    --paper: #ffffff;
    --stage: #e9e7e3;
    --ink-light: #ffffff;
  }
  * { margin: 0; padding: 0; box-sizing: border-box; }
  html, body {
    width: 1200px;
    height: 768px;
    overflow: hidden;
    background: var(--stage);
    font-family: "Tinos", "Times New Roman", serif;
  }
  .canvas {
    position: relative;
    width: 1200px;
    height: 768px;
  }
  .card {
    position: absolute;
    top: 230px;
    width: 540px;
    height: 309px;
    box-shadow: 0 6px 18px rgba(0,0,0,0.18);
    overflow: hidden;
  }

  /* Contact side */
  .card-contact {
    left: 40px;
    background: linear-gradient(160deg, var(--navy) 0%, var(--navy-deep) 100%);
    color: var(--ink-light);
  }
  .contact-block {
    position: absolute;
    top: 34px;
    right: 36px;
    text-align: right;
  }
  .person-name {
    font-size: 22px;
    letter-spacing: 0.5px;
    text-transform: uppercase;
    line-height: 1.1;
  }
  .person-title {
    font-size: 12.5px;
    letter-spacing: 0.6px;
    text-transform: uppercase;
    margin-top: 3px;
  }
  .rule {
    width: 28px;
    height: 1px;
    background: var(--ink-light);
    opacity: 0.8;
    margin: 14px 0 12px auto;
  }
  .address, .details {
    font-size: 13px;
    line-height: 1.4;
  }
  .details dt { display: inline; }
  .details dd { display: inline; }
  .details div { white-space: nowrap; }

  /* Brand side */
  .card-brand {
    left: 620px;
    background: var(--paper);
  }
  .brand-name {
    position: absolute;
    top: 100px;
    left: 0;
    right: 0;
    text-align: center;
    color: var(--navy-deep);
  }
  .brand-word {
    font-size: 44px;
    letter-spacing: 3px;
    text-transform: uppercase;
    line-height: 1;
  }
  .brand-descriptor {
    font-size: 12px;
    letter-spacing: 11px;
    text-transform: uppercase;
    margin-top: 8px;
    padding-left: 11px;
  }
  .stripe-thin {
    position: absolute;
    left: 0;
    right: 0;
    bottom: 58px;
    height: 9px;
    background: var(--navy);
  }
  .stripe-band {
    position: absolute;
    left: 0;
    right: 0;
    bottom: 14px;
    height: 26px;
    background: var(--navy);
    color: var(--ink-light);
    font-size: 11px;
    letter-spacing: 2px;
    line-height: 26px;
    text-align: right;
    padding-right: 28px;
  }
</style>
</head>
<body>
<main class="canvas">

  <section class="card card-contact" aria-label="Business card contact side">
    <div class="contact-block">
      <h1 class="person-name">Paul Whitcombe</h1>
      <p class="person-title">Managing Partner</p>
      <div class="rule"></div>
      <p class="address">Level 9, 7 Ferris Lane<br>Sydney NSW 2000</p>
      <div class="rule"></div>
      <dl class="details">
        <div><dt>PHONE: </dt><dd>02 9364 2710</dd></div>
        <div><dt>PHONE: </dt><dd>02 8472 3159</dd></div>
        <div><dt>EMAIL: </dt><dd>paul@qvlegal.com.au</dd></div>
        <div><dt>WEB: </dt><dd>www.qvlegal.com.au</dd></div>
      </dl>
    </div>
  </section>

  <section class="card card-brand" aria-label="Business card brand side">
    <div class="brand-name">
      <div class="brand-word">Quayvale</div>
      <div class="brand-descriptor">Lawyers</div>
    </div>
    <div class="stripe-thin"></div>
    <div class="stripe-band">www.qvlegal.com.au</div>
  </section>

</main>
</body>
</html>
```